Wedding Invitations

We are a printing company "inkhollow" and require multiple wedding invitation designs for our customers in store and online. We would like the designs to be editable in Photoshop if possible, if not then a layout with suggested fonts would be the next best option. We are open to suggestions on design but would like to stick to the general wedding themes some with a modern and some with a classical feel

Industry/Entity Type

Printing

```html
<!DOCTYPE html>
<html lang="en">
<head>
<meta charset="utf-8">
<title>Wedding Invitation – Victoria and David</title>
<link href="https://fonts.googleapis.com/css2?family=Dawning+of+a+New+Day&family=Della+Respira&display=swap" rel="stylesheet">
<style>
  :root {
    --mint: #9feccf;
    --paper: #caf4e3;
    --paper-light: #e4f9f1;
    --ink: #1f2322;
    --ink-soft: #6f7d78;
    --monogram: #b9c9c2;
  }
  html, body {
    margin: 0;
    padding: 0;
    overflow: hidden;
    background: var(--mint);
  }
  .invitation {
    position: relative;
    width: 880px;
    height: 1200px;
    overflow: hidden;
    background: var(--mint);
  }
  .papel-picado {
    position: absolute;
    inset: 0;
  }
  .monogram {
    position: absolute;
    left: 335px;
    top: 108px;
    width: 180px;
    height: 135px;
    border-radius: 50%;
    background: radial-gradient(ellipse at center, var(--monogram) 0%, rgba(185,201,194,0.25) 65%, rgba(185,201,194,0) 100%);
  }
  .text {
    position: absolute;
    left: 0;
    width: 880px;
    margin: 0;
    text-align: center;
    color: var(--ink);
    font-family: "Dawning of a New Day", cursive;
    line-height: 1;
  }
  .hosts { top: 322px; font-size: 34px; line-height: 40px; }
  .request { top: 474px; font-size: 27px; line-height: 31px; color: var(--ink-soft); }
  .couple {
    top: 598px;
    font-family: "Della Respira", serif;
    font-size: 68px;
    line-height: 80px;
  }
  .date { top: 770px; font-size: 31px; line-height: 31px; }
  .time { top: 838px; font-size: 36px; line-height: 36px; }
  .venue { top: 1004px; font-size: 31px; line-height: 32px; }
</style>
</head>
<body>
<main class="invitation">
  <svg class="papel-picado" width="880" height="1200" viewBox="0 0 880 1200" role="img" aria-label="Cut paper papel picado sheet with floral and leaf pattern in pale mint">
    <rect x="20" y="20" width="840" height="1160" rx="18" fill="var(--paper)"/>
    <rect x="110" y="270" width="660" height="660" rx="120" fill="var(--paper-light)"/>
  </svg>

  <div class="monogram" role="img" aria-label="Hand-drawn V and D monogram"></div>

  <p class="text hosts">Charles and Monica Smith<br>and<br>Andrew and Catherine Jones</p>
  <p class="text request">Request the honor of your presence<br>at the marriage of their children</p>
  <h1 class="text couple">Victoria and David</h1>
  <p class="text date">Saturday the fourteenth of September<br>Two thousand and thirteen</p>
  <p class="text time">4 o’clock in the afternoon</p>
  <p class="text venue">Lantern Garden<br>in Willow Park<br>Ashbury, Vermont</p>
</main>
</body>
</html>
```